Business Card Design Project

Actor, Producer, Vocal Coach, Choral Director, Song WriterPhone: (215) 555-0142 Fax: (215) 856-3933Email: waltierblocker@gmail.comFacebook: facebook.com/waltier.blockerTwitter: @thedf482

Industry/Entity Type

Business

Contact Information for Business Card

Business Cards that include my picture

Colors

Designer to choose colors to be used in the design.

```html
<!DOCTYPE html>
<html lang="en">
<head>
<meta charset="utf-8">
<title>Dorian Fellsmore – Business Card</title>
<link href="https://fonts.googleapis.com/css2?family=Montserrat:wght@400;500;700&display=swap" rel="stylesheet">
<style>
  :root {
    --backdrop: #111111;
    --card-black: #050505;
    --card-white: #ffffff;
    --ink: #111111;
    --ink-soft: #2a2a2a;
    --divider: #d6d6d6;
    --panel-tint: #f6f6f6;
    --photo-light: #c9bfc4;
    --photo-dark: #8f858b;
    --social-a: #3b5998;
    --social-b: #55acee;
  }
  * { margin: 0; padding: 0; box-sizing: border-box; }
  html, body { width: 1200px; height: 1000px; overflow: hidden; }
  body {
    background: var(--backdrop);
    font-family: "Montserrat", Arial, sans-serif;
    position: relative;
  }
  .card {
    position: absolute;
    top: 356px;
    width: 504px;
    height: 288px;
    border-radius: 22px;
    overflow: hidden;
  }
  .card-back {
    left: 70px;
    background: var(--card-black);
    display: flex;
    align-items: center;
    justify-content: center;
  }
  .monogram {
    color: var(--card-white);
    font-weight: 700;
    font-size: 64px;
    letter-spacing: 2px;
  }
  .card-front {
    left: 626px;
    background: var(--card-white);
  }
  .portrait {
    position: absolute;
    left: 16px;
    top: 20px;
    width: 222px;
    height: 216px;
    background: linear-gradient(160deg, var(--photo-light), var(--photo-dark));
  }
  .divider {
    position: absolute;
    left: 238px;
    top: 20px;
    width: 8px;
    height: 268px;
    background: var(--divider);
  }
  .details {
    position: absolute;
    left: 246px;
    top: 0;
    right: 0;
    bottom: 0;
    background: var(--panel-tint);
    padding: 68px 20px 0 0;
    text-align: right;
    color: var(--ink);
  }
  .name { font-size: 22px; font-weight: 700; line-height: 1.1; }
  .roles { font-size: 11.5px; font-weight: 500; color: var(--ink-soft); line-height: 1.3; margin-top: 2px; }
  .contacts { list-style: none; margin-top: 20px; }
  .contacts li {
    display: flex;
    justify-content: flex-end;
    align-items: center;
    gap: 6px;
    font-size: 12.5px;
    line-height: 19px;
  }
  .icon {
    width: 14px; height: 14px;
    border-radius: 50%;
    background: var(--ink);
    display: inline-flex;
    align-items: center;
    justify-content: center;
    flex: none;
  }
  .icon svg { width: 9px; height: 9px; }
  .icon-social-a { background: var(--social-a); }
  .icon-social-b { background: var(--social-b); }
</style>
</head>
<body>
  <section class="card card-back" aria-label="Card back">
    <span class="monogram">DF</span>
  </section>

  <section class="card card-front" aria-label="Card front">
    <div class="portrait" role="img" aria-label="Portrait photo of Dorian Fellsmore in a grey suit and pink tie"></div>
    <div class="divider"></div>
    <div class="details">
      <h1 class="name">Dorian Fellsmore</h1>
      <p class="roles">Actor, Producer, Vocal Coach<br>Choral Director, Song Writer</p>
      <ul class="contacts">
        <li>(215) 555-0142
          <span class="icon"><svg viewBox="0 0 10 10"><path d="M2 1h2l1 2-1 1c.5 1 1 1.5 2 2l1-1 2 1v2c-4 0-7-3-7-7z" fill="#fff"/></svg></span>
        </li>
        <li>(215) 555-0187
          <span class="icon"><svg viewBox="0 0 10 10"><rect x="1.5" y="3" width="7" height="5" fill="#fff"/><rect x="3" y="1.5" width="4" height="2" fill="#fff"/></svg></span>
        </li>
        <li>dorianfellsmore@postlane.net
          <span class="icon"><svg viewBox="0 0 10 10"><rect x="1.5" y="2.5" width="7" height="5" fill="none" stroke="#fff"/><path d="M1.5 2.5l3.5 3 3.5-3" fill="none" stroke="#fff"/></svg></span>
        </li>
        <li>dorian.fellsmore <span class="icon icon-social-a"></span></li>
        <li>@thedf482 <span class="icon icon-social-b"></span></li>
      </ul>
    </div>
  </section>
</body>
</html>
```